Bookcover: Ways to Turn Into a Bold Pathfinder

I am publishing a super-low-cost innovation book for €4,99 on Quillmere Open Press to help everyone become a great innovator: young ambitious people without college education nor a big budget. Do you want to help me?

Brief:
Design a book cover 1600 x 2560 pixels for QOP.
Main title: Ways to Turn Into a Bold Pathfinder
Sub title: mindset - insights - skills & tools
Author: Joost ter Brakel
Design: captive, and appealing to everyone
Target Group: young ambitious people without college education

For quillmere please format the height/width ratio of 1.6:1

```html
<!DOCTYPE html>
<html lang="en">
<head>
<meta charset="utf-8">
<title>Ways to Turn Into a Bold Pathfinder — Book Cover</title>
<link rel="stylesheet" href="https://fonts.googleapis.com/css2?family=Montserrat:wght@500;600;700;800&display=swap">
<style>
  :root {
    --backdrop: #8c8c8c;
    --cover-top: #e9b63c;
    --cover-bottom: #dca12b;
    --ink: #363636;
    --accent: #7a2b42;
    --band: #2b2b2b;
    --band-text: #f4f4f4;
    --beam: rgba(255, 255, 255, 0.85);
  }
  * { margin: 0; padding: 0; box-sizing: border-box; }
  html, body {
    width: 1200px;
    height: 1200px;
    overflow: hidden;
    background: var(--backdrop);
  }
  .book-cover {
    position: absolute;
    left: 233px;
    top: 81px;
    width: 734px;
    height: 1038px;
    background: linear-gradient(180deg, var(--cover-top) 0%, var(--cover-bottom) 100%);
    overflow: hidden;
    font-family: "Montserrat", sans-serif;
    color: var(--ink);
  }
  .spotlight {
    position: absolute;
    inset: 0;
    width: 734px;
    height: 600px;
  }
  .hero-illustration {
    position: absolute;
    left: 188px;
    top: 130px;
    width: 332px;
    height: 294px;
    border-radius: 40px;
    background: radial-gradient(circle at 50% 45%, #4a4a4a 0%, #3d3d3d 60%, rgba(61,61,61,0.85) 100%);
  }
  .title-lead,
  .title-main,
  .subtitle-item {
    position: absolute;
    left: 0;
    width: 100%;
    text-align: center;
    white-space: nowrap;
  }
  .title-lead {
    top: 478px;
    font-size: 32px;
    font-weight: 700;
    letter-spacing: 2.5px;
  }
  .title-main {
    top: 510px;
    font-size: 80px;
    font-weight: 800;
    letter-spacing: 6px;
    color: var(--accent);
    line-height: 1.2;
  }
  .subtitle-item {
    font-size: 32px;
    font-weight: 500;
    letter-spacing: 4px;
    line-height: 1;
  }
  .subtitle-item.mindset { top: 670px; }
  .subtitle-item.insights { top: 774px; }
  .subtitle-item.skills { top: 886px; }
  .author-band {
    position: absolute;
    left: 0;
    bottom: 0;
    width: 100%;
    height: 55px;
    background: var(--band);
    display: flex;
    align-items: center;
    justify-content: center;
  }
  .author-name {
    color: var(--band-text);
    font-size: 23px;
    font-weight: 600;
    letter-spacing: 2.5px;
    text-transform: uppercase;
  }
</style>
</head>
<body>
  <main class="book-cover">
    <svg class="spotlight" viewBox="0 0 734 600" aria-hidden="true">
      <defs>
        <linearGradient id="beamFade" x1="0" y1="0" x2="0" y2="1">
          <stop offset="0" stop-color="#ffffff" stop-opacity="0.9"/>
          <stop offset="0.45" stop-color="#ffffff" stop-opacity="0.35"/>
          <stop offset="1" stop-color="#ffffff" stop-opacity="0"/>
        </linearGradient>
      </defs>
      <polygon points="228,0 508,0 724,470 10,470" fill="url(#beamFade)"/>
    </svg>

    <div class="hero-illustration" role="img" aria-label="Light bulb with circuit filament and two interlocking gears"></div>

    <h1>
      <span class="title-lead">Ways to Turn Into a Bold</span>
      <span class="title-main">Pathfinder</span>
    </h1>

    <p class="subtitle-item mindset">Mindset</p>
    <p class="subtitle-item insights">Insights</p>
    <p class="subtitle-item skills">Skills &amp; Tools</p>

    <footer class="author-band">
      <span class="author-name">Joost ter Brakel</span>
    </footer>
  </main>
</body>
</html>
```